Heritage Hollow Business Cards

Require a business card design. <br/><br/>Needs to include logo (either round or long version) plus these details:<br/>Maya Torvell<br/>Heritage Hollow<br/>maya@kelvadtrading.com.au<br/>02 6481 7395<br/>PO Box Glenwarra NSW 2791<br/>www.heritagehollow.com.au<br/><br/>I need in an editable format so that I can create for multiple staff members. <br/><br/>

Target Market(s)

We are an online store selling renovation products to home owners are builders. Looking for a classic classy design.

Industry/Entity Type

Home And Garden

Contact Information for Business Card

Maya Torvell
Heritage Hollow
maya@kelvadtrading.com.au
02 6481 7395
PO Box Glenwarra NSW 2791
www.heritagehollow.com.au

Colors

Designer to choose colors to be used in the design.

Requirements
Must have
• Must include Logo.

```html
<!DOCTYPE html>
<html lang="en">
<head>
<meta charset="utf-8">
<title>Heritage Hollow Business Cards</title>
<link rel="stylesheet" href="https://fonts.googleapis.com/css2?family=Merriweather:wght@300;400;700&display=swap">
<style>
  :root {
    --stage: #1b1c1e;
    --card: #2b2d30;
    --card-deep: #232528;
    --ink: #f1f1f1;
    --ink-soft: #c9cacc;
    --line: #8d8f93;
  }
  * { box-sizing: border-box; margin: 0; padding: 0; }
  html, body {
    width: 1200px; height: 800px; overflow: hidden;
    background: var(--stage);
    font-family: "Merriweather", Georgia, serif;
    color: var(--ink);
  }
  .sheet {
    width: 1200px; height: 800px;
    display: flex; flex-direction: column;
    align-items: center; justify-content: center; gap: 48px;
  }
  .card {
    position: relative;
    width: 560px; height: 320px;
    background: var(--card);
    border-radius: 4px;
    overflow: hidden;
    box-shadow: 0 10px 30px rgba(0,0,0,.45);
  }
  .brand {
    display: flex; align-items: center; gap: 14px;
  }
  .brand-mark {
    width: 46px; height: 46px;
    border: 1.5px solid var(--ink);
    border-radius: 50%;
    flex: none;
  }
  .brand-name {
    font-weight: 400;
    font-size: 32px;
    letter-spacing: .5px;
    color: var(--ink);
    white-space: nowrap;
  }
  .card--front {
    display: flex; align-items: center; justify-content: center;
  }
  .card--back .brand {
    position: absolute; left: 40px; top: 48px;
  }
  .card--back .brand-mark { width: 38px; height: 38px; }
  .card--back .brand-name { font-size: 26px; }
  .sketch-panel {
    position: absolute; right: 0; top: 0;
    width: 190px; height: 100%;
    background: linear-gradient(160deg, var(--card) 0%, var(--card-deep) 55%, #1d1f22 100%);
    border-left: 1px solid rgba(141,143,147,.25);
  }
  .contact {
    position: absolute; left: 40px; bottom: 36px;
    line-height: 1.55;
  }
  .person-name {
    font-weight: 700; font-size: 17px; letter-spacing: .3px;
  }
  .person-role {
    font-weight: 300; font-size: 12px; color: var(--ink-soft);
    margin-bottom: 14px;
  }
  .contact-line {
    font-weight: 300; font-size: 11.5px; color: var(--ink-soft);
  }
  .contact-line b { font-weight: 700; color: var(--ink); }
  .web-domain { font-weight: 700; color: var(--ink); }
</style>
</head>
<body>
<main class="sheet">
  <section class="card card--front">
    <div class="brand">
      <span class="brand-mark"></span>
      <span class="brand-name">Heritage Hollow</span>
    </div>
  </section>

  <section class="card card--back">
    <div class="sketch-panel" role="img" aria-label="Hand-sketched roofline illustration in dark ink"></div>
    <div class="brand">
      <span class="brand-mark"></span>
      <span class="brand-name">Heritage Hollow</span>
    </div>
    <div class="contact">
      <p class="person-name">Maya Torvell</p>
      <p class="person-role">Managing Director</p>
      <p class="contact-line"><b>Phone:</b> 02 6481 7395 | <b>Email:</b> maya@kelvadtrading.com.au</p>
      <p class="contact-line">PO Box Glenwarra NSW 2791</p>
      <p class="contact-line">www.<span class="web-domain">heritagehollow</span>.com.au</p>
    </div>
  </section>
</main>
</body>
</html>
```